KRL Stationery Design Project

Dear Designers,
We need a new stationery design for company to match our new logo.
Designers should provide a design for the following:
1. Business Card: 3.5x2 Inches.
2. Letterhead: A4 size.
3. Envelops: 25x35.5 Cm.
You can keep the Arabic name at the bottom of the logo Or you can use the separate attached Arabic Name.
Please refer to the attached logo guide for design information.
Sample Business Card information:
Name: Tarek Sowan
Position: Operation Manager
Tel: +966 920007164 Ex. 500
Fax: +966 (3)8842617
Mob: +966 (5)00263817
email: tarek@krl-example.com.sa
URL: www.krl-example.com.sa
Address:
Nakheel Heights, Suite 718
Zayed bin Omar Str.
Khobar, 31847
Saudi Arabia
Updates
Dear All,
Please note, we had uploaded our logo along with Arabic writing in Adobe illustrator format (.ai).
Regards,
Karim
Dear All,
A sample data for the business card had been added as per your request.
Regards,
Karim

```html
<!DOCTYPE html>
<html lang="en">
<head>
<meta charset="utf-8">
<title>KRL Business Card</title>
<link rel="stylesheet" href="https://fonts.googleapis.com/css2?family=Play:wght@400;700&display=swap">
<style>
  :root {
    --backdrop: #2a2a2a;
    --card: #ffffff;
    --navy: #10294a;
    --ink: #3a3a3a;
    --rule: #b9b9b9;
    --mark: #8c8c8c;
  }
  * { box-sizing: border-box; margin: 0; padding: 0; }
  html, body { width: 1200px; height: 472px; overflow: hidden; }
  body { background: var(--backdrop); font-family: "Play", sans-serif; color: var(--ink); position: relative; }

  .card {
    position: absolute; top: 84px; width: 525px; height: 299px;
    background: var(--card); border-radius: 14px; overflow: hidden;
  }
  .card--front { left: 50px; }
  .card--back { left: 613px; }

  .brand { position: absolute; display: flex; align-items: center; gap: 12px; }
  .brand__square { width: 18px; height: 18px; background: var(--mark); }
  .brand__name { font-weight: 700; color: var(--navy); line-height: 1; letter-spacing: 2px; }
  .card--front .brand { left: 36px; top: 46px; }
  .card--front .brand__name { font-size: 64px; }
  .card--back .brand { left: 50%; top: 98px; transform: translateX(-50%); }
  .card--back .brand__name { font-size: 72px; }

  .name-rule { position: absolute; top: 144px; height: 1px; background: var(--rule); }
  .name-rule--left { left: 0; width: 366px; }
  .name-rule--right { left: 490px; width: 35px; }
  .person { position: absolute; right: 40px; top: 128px; text-align: right; }
  .person__name { font-weight: 700; font-size: 18px; color: #444; letter-spacing: 1px; }
  .person__title { font-size: 12px; color: #555; margin-top: 2px; letter-spacing: 0.5px; }

  .contacts { position: absolute; right: 46px; top: 177px; list-style: none; text-align: right; }
  .contacts li { font-size: 12.5px; line-height: 17.5px; letter-spacing: 0.6px; display: flex; justify-content: flex-end; align-items: center; gap: 5px; }
  .contacts svg { width: 11px; height: 11px; }

  .address { position: absolute; right: 48px; top: 249px; text-align: right; font-size: 12.5px; line-height: 17.5px; letter-spacing: 0.6px; font-style: normal; }

  .back-url { position: absolute; left: 0; right: 0; top: 240px; text-align: center; font-size: 12.5px; letter-spacing: 1px; }
</style>
</head>
<body>
  <section class="card card--front" aria-label="Business card front">
    <div class="brand"><span class="brand__square"></span><span class="brand__name">KRL</span></div>
    <div class="name-rule name-rule--left"></div>
    <div class="name-rule name-rule--right"></div>
    <div class="person">
      <p class="person__name">Your Name</p>
      <p class="person__title">Title</p>
    </div>
    <ul class="contacts">
      <li>123-456-7890
        <svg viewBox="0 0 12 12" aria-hidden="true"><circle cx="6" cy="6" r="6" fill="var(--navy)"/><path d="M4 3.2c.6 2.4 2 4 4.2 5l.6-.9-1.2-.8-.6.5c-.8-.5-1.4-1.2-1.8-2l.5-.6-.8-1.2z" fill="#fff"/></svg></li>
      <li>123-456-7890
        <svg viewBox="0 0 12 12" aria-hidden="true"><path d="M2.5 5l1-2.5h5l1 2.5h1v3.5h-1.5v1h-1.5v-1h-3v1H3v-1H1.5V5z" fill="var(--navy)"/></svg></li>
      <li>info@mail-example.com
        <svg viewBox="0 0 12 12" aria-hidden="true"><circle cx="6" cy="6" r="6" fill="var(--navy)"/><rect x="3" y="4" width="6" height="4.2" fill="#fff"/><path d="M3 4l3 2.3L9 4" stroke="var(--navy)" stroke-width=".8" fill="none"/></svg></li>
      <li>www.website.com
        <svg viewBox="0 0 12 12" aria-hidden="true"><circle cx="6" cy="6" r="6" fill="var(--navy)"/><path d="M1 6h10M6 1c-2 2.8-2 7.2 0 10M6 1c2 2.8 2 7.2 0 10" stroke="#fff" stroke-width=".8" fill="none"/></svg></li>
    </ul>
    <address class="address">Street Name, City Name<br>State, City Zip Code</address>
  </section>

  <section class="card card--back" aria-label="Business card back">
    <div class="brand"><span class="brand__square"></span><span class="brand__name">KRL</span></div>
    <p class="back-url">www.website.com</p>
  </section>
</body>
</html>
```